Boutique startup consulting

Hello,
Me and my partner are starting a boutique consulting/ "venturing for startup" firm and want to make professional looking slides. The point of these slide are to attract Automakers's venture arms to collaborate with us. We are hoping to win clients with this presentation.

Acceptance criteria:
1. You put beautiful designs where-ever you can and make the attached slides look professional. Full freedom in designing the slides. You are the artist, please create some magic
2. The style should be innovative and state of the art. It should be with colourful designs
3. The slides should be very professional
4. We are unsure of how to present our previous experience. Please help us out
5. The first slide has gray background. you may use the original colored image and tweak it

Here is out website:
https://www.talvora-partners.net/

Can you please ensure that the slides are presented in the following format?

PRESENTATION
1. Starting Masterslide
2. Customized Starting Masterslide (with Topic + Customer Logo, for eg. Smart City & KDR)
3. Service Categories Masterslide /Overview ( we have 5 Categories which are shown by icon and buzzword, see https://www.talvora-partners.net/live/research-strategy/research-strategy.aspx, this is for eg. the Overview for the categorie “Research &Strategy”. We have 2-4 Icon per Category, other categories are Business Development,Venture Building, Expansion Advisory, Sustainable Due Diligence , see webside)
4. Subcategories & Description Masterslide
o We have 15 Subcategories, the Masterslide should just show the Icon and then 1-2 square for description with bullets, f.ex. https://www.talvora-partners.net/live/expansion-advisory-feasibility-analysis/feasibility-analysis.aspx
5. Team Presenting Masterslide
o Not like Website, a Masterslide where each Teammember can present him self, in bullets with Education/Business Experience/ other awards/distinction AND in Text bubbles like “Experiences and hands-on Business developer”
6. Contact ( closing Chart with contact data, liked in etc.)
7. Masterslide (free for individual content)
o Just a slide with the CI framework which can be used as Masterslide for other charts like

8. PROPOSAL Masterslide (like customized starting slide, but Proposal)
9. Background Masterslide (Text)
o A textual description
10. Value Proposition & Goals Masterslide (Text & Bullets)
o V P will be textual so for eg. text frame; Goals with 2-4 squares (text/Bullets) for sub-goals and including the tasks for these goals in bullets
11. Milestones & Timing Masterslide (Timeline , Squares & text)
o Timeline, for eg. 6 Month project, where we have 8 tasks with starting and ending
12. Free MAsterslide /Proposal
o Where we can add charts to the proposal like Conditions or Contact

To Add:
- Logo colour description
- Picture and Icons ( so they don’t need to buy new pics or look for them)

Requirements
Must have
• Please check out the slides and make them presentable

```html
<!DOCTYPE html>
<html lang="en">
<head>
<meta charset="utf-8">
<title>Team – Anselm Kröger</title>
<link href="https://fonts.googleapis.com/css2?family=Fira+Sans:wght@300;400;500;600;700&display=swap" rel="stylesheet">
<style>
  :root{
    --green:#a5c93b;
    --light:#eeeeee;
    --mid:#818181;
    --dark:#1b1b1b;
    --text:#333333;
    --muted:#707070;
    --bar:#454545;
    --white:#ffffff;
  }
  *{margin:0;padding:0;box-sizing:border-box}
  html,body{width:1200px;height:675px;overflow:hidden;background:var(--white)}
  body{font-family:"Fira Sans",sans-serif;color:var(--text)}
  .slide{position:relative;width:1200px;height:675px;overflow:hidden;background:var(--white)}
  .upper{position:absolute;left:0;top:0;width:662px;height:388px;background:var(--light)}
  .lower{position:absolute;left:0;top:388px;width:662px;height:287px;background:var(--mid)}
  .portrait{position:absolute;left:0;top:50px;width:250px;height:299px;
    background:linear-gradient(160deg,#d9dbdc 0%,#c9cbcc 55%,#9a8468 85%,#7d6a52 100%)}
  .spine-green{position:absolute;left:308px;top:50px;width:5px;height:338px;background:var(--green)}
  .spine-white{position:absolute;left:308px;top:388px;width:5px;height:202px;background:var(--white)}
  .icon-pill{position:absolute;left:292px;top:205px;width:36px;height:135px;background:var(--green);border-radius:4px}
  .icon-pill svg{position:absolute;left:8px;width:20px;height:20px}
  .name{position:absolute;left:348px;top:96px;font-size:30px;color:var(--green);font-weight:400;white-space:nowrap}
  .name strong{font-weight:600}
  .role{position:absolute;left:349px;top:139px;font-size:14px;letter-spacing:1.4px;color:var(--muted);font-weight:400}
  .contact{position:absolute;left:347px;font-size:16px;color:var(--text);line-height:17px}
  .highlights{position:absolute;left:62px;top:428px;list-style:none;color:var(--white);font-size:16px;line-height:20px}
  .highlights li{position:relative;padding-left:28px;margin-bottom:9px}
  .highlights svg{position:absolute;left:0;top:2px;width:18px;height:18px}
  .summary{position:absolute;left:347px;top:428px;width:257px;font-size:14.6px;line-height:19px;color:var(--white);text-align:justify}
  .summary p+p{margin-top:5px}
  .breadcrumb{position:absolute;left:0;top:632px;height:27px;width:590px;background:var(--bar);display:flex;align-items:center;color:var(--white);font-size:15px;letter-spacing:.3px}
  .page-no{width:60px;height:27px;background:var(--green);display:flex;align-items:center;justify-content:center;font-weight:700;font-size:17px}
  .breadcrumb .path{padding-left:12px}
  .breadcrumb b{font-weight:600}
  .breadcrumb .current{color:var(--green);font-weight:600}
  .rail{position:absolute;left:662px;top:0;width:116px;height:675px;background:var(--dark)}
  .band{position:absolute;left:662px;width:538px;height:32px;background:var(--green);color:var(--white);font-weight:500;font-size:18px;letter-spacing:.5px;padding-left:154px;line-height:32px}
  .badges{position:absolute;left:662px;top:0;width:116px;height:675px}
  .entry{position:absolute;left:816px;width:300px;font-size:14px;line-height:18px}
  .entry h3{font-size:15.6px;font-weight:500;color:#3a3a3a;margin-bottom:1px}
  .entry p{color:#4a4a4a}
  .divider{position:absolute;left:816px;width:297px;height:1px;background:var(--green)}
  .brand{position:absolute;left:979px;top:623px;display:flex;align-items:center;gap:4px}
  .brand-dot{width:24px;height:24px;border-radius:50%;background:var(--green)}
  .brand-name{font-size:17px;font-weight:500;color:var(--green);letter-spacing:.3px}
</style>
</head>
<body>
<div class="slide">
  <div class="upper"></div>
  <div class="lower"></div>
  <div class="portrait" role="img" aria-label="Portrait photo of Anselm Kröger"></div>

  <div class="spine-green"></div>
  <div class="spine-white"></div>
  <div class="icon-pill">
    <svg style="top:10px" viewBox="0 0 20 20" fill="none" stroke="#fff" stroke-width="1.4"><path d="M10 18s-6-6-6-10a6 6 0 0 1 12 0c0 4-6 10-6 10z"/><circle cx="10" cy="8" r="2.2"/></svg>
    <svg style="top:52px" viewBox="0 0 20 20" fill="none" stroke="#fff" stroke-width="1.4"><rect x="2" y="5" width="16" height="11"/><path d="M2 5l8 6 8-6M2 16l6-5M18 16l-6-5"/></svg>
    <svg style="top:77px" viewBox="0 0 20 20" fill="none" stroke="#fff" stroke-width="1.4"><path d="M4 17c-1-2 0-8 5-12 3-2 6-2 7-1l-2 3-3-1c-3 2-4 5-4 7l2 2-3 3z"/></svg>
    <svg style="top:102px" viewBox="0 0 20 20" fill="none" stroke="#fff" stroke-width="1.3"><circle cx="10" cy="10" r="7.5"/><ellipse cx="10" cy="10" rx="3.5" ry="7.5"/><path d="M2.5 10h15M4 6h12M4 14h12"/></svg>
  </div>

  <div class="name">Anselm <strong>Kröger</strong></div>
  <div class="role">FOUNDER &amp; MANAGING DIRECTOR</div>

  <div class="contact" style="top:214px">Talvora Partners GmbH,<br>Lindenhofstrasse 14, D-10117, Berlin</div>
  <div class="contact" style="top:256px">kroeger@talvora-partners.net</div>
  <div class="contact" style="top:282px">(+49) 151 2738 5046</div>
  <div class="contact" style="top:307px">talvora-partners.net</div>

  <ul class="highlights">
    <li><svg viewBox="0 0 18 18" fill="none" stroke="#fff" stroke-width="1.2"><rect x="6" y="1.5" width="6" height="10" rx="3"/><path d="M3.5 8.5a5.5 5.5 0 0 0 11 0M9 14v3"/></svg>Lorem ipsum dolor sit<br>amet laoreet aliquae</li>
    <li><svg viewBox="0 0 18 18" fill="none" stroke="#fff" stroke-width="1.2"><circle cx="9" cy="10" r="7"/><path d="M9 3v7H2"/></svg>Conseceur elit adispo<br>nti aed&nbsp; am nonummy</li>
    <li><svg viewBox="0 0 18 18" fill="none" stroke="#fff" stroke-width="1.2"><path d="M2 4l5-2 4 2 5-2v12l-5 2-4-2-5 2z M7 2v12M11 4v12"/></svg>Euismod tincidunt ut<br>laoreet dolore nisl</li>
  </ul>

  <div class="summary">
    <p>Consectetuer elit adipiscing, sed diam nonummy ex nibh. Euismod tincidunt ut laoreet dolore magna aliquam erat.</p>
    <p>Exerci ottatation ullamcorper suscipit lobortis ut nonummy aliquip exea commodo.</p>
  </div>

  <div class="breadcrumb">
    <div class="page-no">06</div>
    <div class="path">SMART MOBILITY &amp; KDR &gt;&gt; <b>TEAM</b> &gt;&gt; <span class="current">ANSELM KRÖGER</span></div>
  </div>

  <div class="rail"></div>
  <div class="band" style="top:50px">EDUCATION</div>
  <div class="band" style="top:344px">EXPERIENCE</div>

  <svg class="badges" viewBox="0 0 116 675" font-family="Fira Sans, sans-serif" font-size="9" font-weight="500" text-anchor="middle">
    <path d="M60 128V280M60 423V556" stroke="#fff" stroke-width="2"/>
    <g fill="#fff"><circle cx="60" cy="128" r="26"/><circle cx="60" cy="211" r="26"/><circle cx="60" cy="280" r="26"/>
      <circle cx="60" cy="423" r="26"/><circle cx="60" cy="489" r="26"/><circle cx="60" cy="556" r="26"/></g>
    <g fill="#333"><text x="60" y="131">Lumen</text><text x="60" y="214">Hallberg</text><text x="60" y="283">Corvane</text>
      <text x="60" y="426">Meridia</text><text x="60" y="492">Verdant</text><text x="60" y="559">Talvora</text></g>
  </svg>

  <div class="entry" style="top:104px"><h3>1993: Diplome d’information</h3><p>Lumen Press Institute, University of<br>Valcourt</p></div>
  <div class="divider" style="top:179px"></div>
  <div class="entry" style="top:193px"><h3>1995: Masters in Media &amp; Communication</h3><p>Hallberg University, Munich</p></div>
  <div class="divider" style="top:245px"></div>
  <div class="entry" style="top:262px"><h3>2004: Corvane Executive MBA</h3><p>Corvane Business School</p></div>

  <div class="entry" style="top:400px"><h3>1997–00: Publishing Director</h3><p>Meridia Magazine</p></div>
  <div class="divider" style="top:453px"></div>
  <div class="entry" style="top:469px"><h3>2001–2003: Managing Director</h3><p>Verdant Review Publishing House</p></div>
  <div class="divider" style="top:521px"></div>
  <div class="entry" style="top:538px"><h3>2004 to date: Founder &amp; MD</h3><p>Talvora Partners</p></div>

  <div class="brand"><span class="brand-dot"></span><span class="brand-name">TALVORA PARTNERS</span></div>
</div>
</body>
</html>
```